Willow Creek Gatherings Event Planning in need of a design!!

Event Planning company, does a variety of events. I like simple more rustic designs focused on almond blossoms. We are based out of Northern California, the heart of almond country. I would like to see colors in light pinks, beige, light browns, whites or creams. the final design should communicate rustic simplicity. Below are some pictures of Almond blossoms and design ideas I prefer the one called Tulip Grove. Thanks

Target Market(s)

Women in the mid twenties and older. They should be in the upper middle class in need of an amazing party design and coordinator

Industry/Entity Type

Event Planning

Contact Information for Business Card

Maren Lockwood 530-624-0295almondbaffairs@gmail.comalmondblossomaffairs.com

Font styles to use
Other font styles liked:
• Amatic SC

Requirements
Must have
• almond blossom
• my information
• simplicity
Nice to have
• rustic design
• vintage feel
• whimsical
Should not have
• i like pink but not over the top

```html
<!DOCTYPE html>
<html lang="en">
<head>
<meta charset="utf-8">
<title>Willow Creek Gatherings – Business Card</title>
<link rel="stylesheet" href="https://fonts.googleapis.com/css2?family=Open+Sans:wght@400;600&display=swap">
<style>
  :root {
    --stage: #000000;
    --card: #ffffff;
    --brand: #8a6a4a;
    --brand-soft: #efe6dc;
    --ink: #1e1e1e;
    --sky: #3f78c4;
    --sky-light: #bcd3ee;
    --blossom: #f3f1ee;
    --branch: #6d5a48;
  }
  * { margin: 0; padding: 0; box-sizing: border-box; }
  html, body {
    width: 1200px; height: 900px; overflow: hidden;
    background: var(--stage);
    font-family: "Open Sans", Arial, sans-serif;
  }
  .stage { position: relative; width: 1200px; height: 900px; }

  .card { position: absolute; top: 275px; width: 477px; height: 293px; overflow: hidden; }
  .card--front { left: 116px; background: var(--card); border-radius: 0 52px 0 52px; }
  .card--back { left: 622px; border-radius: 52px 0 52px 0; }

  .ornament-slot {
    position: absolute; border-radius: 20px;
    background: radial-gradient(ellipse at center, var(--brand-soft) 0%, rgba(239,230,220,0) 75%);
  }
  .card--front .ornament-slot { left: 52px; top: 66px; width: 150px; height: 52px; }

  .brand-name {
    position: absolute; color: var(--brand); font-weight: 400;
    letter-spacing: 0.5px; line-height: 1.15;
  }
  .card--front .brand-name { left: 26px; top: 124px; font-size: 28px; width: 260px; }

  .person-name {
    position: absolute; right: 28px; top: 36px;
    color: var(--brand); font-weight: 600; font-size: 16.5px;
  }

  .contact-list { position: absolute; right: 26px; top: 206px; list-style: none; }
  .contact-list li {
    display: flex; align-items: center; justify-content: flex-end;
    height: 19.5px; font-size: 13px; color: var(--ink);
  }
  .contact-list svg { width: 11px; height: 11px; margin-left: 11px; fill: var(--brand); }

  .blossom-photo {
    position: absolute; inset: 0;
    background:
      radial-gradient(ellipse 40% 45% at 30% 45%, var(--blossom) 0%, rgba(243,241,238,0) 100%),
      radial-gradient(ellipse 30% 30% at 85% 65%, var(--blossom) 0%, rgba(243,241,238,0) 100%),
      radial-gradient(ellipse 50% 30% at 70% 20%, #e9eef4 0%, rgba(233,238,244,0) 100%),
      linear-gradient(160deg, var(--sky-light) 0%, var(--sky) 55%, var(--branch) 130%);
  }
  .card--back .ornament-slot { left: 310px; top: 18px; width: 120px; height: 42px; }
  .card--back .brand-name {
    right: 30px; top: 62px; font-size: 24px; text-align: right; width: 200px;
  }
</style>
</head>
<body>
<main class="stage">
  <section class="card card--front" aria-label="Business card front">
    <div class="ornament-slot" role="img" aria-label="Decorative floral flourish above the company name"></div>
    <p class="brand-name">Willow Creek Gatherings</p>
    <p class="person-name">Maren Lockwood</p>
    <ul class="contact-list">
      <li>530-817-4362
        <svg viewBox="0 0 12 12" aria-hidden="true"><path d="M3 0h6a1 1 0 0 1 1 1v10a1 1 0 0 1-1 1H3a1 1 0 0 1-1-1V1a1 1 0 0 1 1-1zm.5 1.5v8h5v-8z"/></svg>
      </li>
      <li>willowcgather@mailbox.test
        <svg viewBox="0 0 12 12" aria-hidden="true"><path d="M0 2h12v8H0zm1 1v.4l5 3.2 5-3.2V3z"/></svg>
      </li>
      <li>www.willowcreekgatherings.test
        <svg viewBox="0 0 12 12" aria-hidden="true"><circle cx="6" cy="6" r="6"/></svg>
      </li>
    </ul>
  </section>

  <section class="card card--back" aria-label="Business card back">
    <div class="blossom-photo" role="img" aria-label="Photograph of white almond blossoms on a branch against a blue sky"></div>
    <div class="ornament-slot" role="img" aria-label="Decorative floral flourish above the company name"></div>
    <p class="brand-name">Willow Creek Gatherings</p>
  </section>
</main>
</body>
</html>
```